Roofing company in Toronto, Canada needs a logo design and business card design

We need a business card and logo created for our company. Our company is "KLV Roofing" which provides roofing services for commercial and residential customers. We serve customers in the Greater Toronto Area (in Canada) thus the name KLV.

We want the logo and business card to be a modern design displaying professionalism and quality in the work. We would prefer rounded corners for the business cards but are open to other ideas. The cards should be pleasant and appealing to customers.

Target Market(s)

Commercial and Residential customers

Industry/Entity Type

Roofing

Contact Information for Business Card

Logo Text

KLV Roofing

Requirements
Nice to have
• Colours that are pleasing to the eye but at the same time should stand out from other business cards. If the design can incorporate the name of KLV Roofing and the actual concept of roofing that would be nice.
Should not have
• Do not want the business cards or logo to be childish looking. Need to look professionally designed.

```html
<!DOCTYPE html>
<html lang="en">
<head>
<meta charset="utf-8">
<title>KLV Roofing – Business Card</title>
<link rel="stylesheet" href="https://fonts.googleapis.com/css2?family=Montserrat:wght@700;800&family=Open+Sans:wght@400;600&display=swap">
<style>
  :root {
    --backdrop: #3b3430;
    --card: #0d0d0d;
    --card-edge: #1c1c1c;
    --accent: #f2b21b;
    --text-light: #f1f1f1;
    --silver: #c9c9c9;
  }
  * { margin: 0; padding: 0; box-sizing: border-box; }
  html, body {
    width: 1200px;
    height: 900px;
    overflow: hidden;
    background: var(--backdrop);
  }
  .stage {
    position: relative;
    width: 1200px;
    height: 900px;
  }
  .card {
    position: absolute;
    top: 300px;
    width: 520px;
    height: 297px;
    background: var(--card);
    border: 1px solid var(--card-edge);
    border-radius: 8px;
    box-shadow: 0 10px 30px rgba(0,0,0,0.45);
  }
  .card--info { left: 60px; }
  .card--brand { left: 620px; display: flex; align-items: center; justify-content: center; }

  .brand-name {
    font-family: "Montserrat", sans-serif;
    font-weight: 800;
    letter-spacing: 0.5px;
    line-height: 1;
    white-space: nowrap;
  }
  .brand-slot {
    position: absolute;
    left: 24px;
    top: 0;
    width: 212px;
    height: 100%;
    display: flex;
    align-items: center;
    justify-content: center;
  }
  .card--info .brand-name {
    font-size: 25px;
    color: var(--accent);
  }
  .card--brand .brand-name {
    font-size: 50px;
    color: var(--silver);
  }

  .divider {
    position: absolute;
    left: 258px;
    top: 62px;
    width: 1px;
    height: 174px;
    background: linear-gradient(to bottom, transparent, var(--accent), transparent);
  }

  .contact {
    position: absolute;
    left: 280px;
    top: 66px;
    width: 220px;
    font-family: "Open Sans", sans-serif;
    color: var(--text-light);
  }
  .contact__name {
    font-family: "Montserrat", sans-serif;
    font-weight: 800;
    font-size: 16px;
    color: var(--accent);
    text-transform: uppercase;
    letter-spacing: 0.5px;
  }
  .contact__title { font-size: 12px; margin-bottom: 18px; }
  .contact__list { list-style: none; font-size: 13px; line-height: 19px; }
  .contact__list li { display: flex; align-items: center; gap: 8px; }
  .contact__list svg { width: 10px; height: 10px; fill: var(--accent); flex: none; }
  .contact__address { font-size: 13px; line-height: 19px; margin-top: 16px; }
</style>
</head>
<body>
<main class="stage">
  <section class="card card--info">
    <div class="brand-slot"><div class="brand-name">KLV Roofing</div></div>
    <div class="divider"></div>
    <div class="contact">
      <div class="contact__name">Daniel Brooks</div>
      <div class="contact__title">Managing Director</div>
      <ul class="contact__list">
        <li><svg viewBox="0 0 10 10"><path d="M2 0.5 L3.6 2.6 L2.8 3.6 Q4 6 6.4 7.2 L7.4 6.4 L9.5 8 L8.4 9.5 Q4.5 9 1.5 5.5 Q0.5 3.5 0.5 1.6 Z"/></svg>(044)123456789</li>
        <li><svg viewBox="0 0 10 10"><path d="M0.5 2 H9.5 V8 H0.5 Z M0.5 2 L5 5.5 L9.5 2" stroke="#0d0d0d" stroke-width="0.8"/></svg>info@youremail.com</li>
        <li><svg viewBox="0 0 10 10"><circle cx="5" cy="5" r="4.5"/><path d="M0.5 5 H9.5 M5 0.5 V9.5" stroke="#0d0d0d" stroke-width="0.7"/></svg>www.websitename.com</li>
      </ul>
      <p class="contact__address">1234, Address GoesHere,<br>Country name, 12345</p>
    </div>
  </section>

  <section class="card card--brand">
    <div class="brand-name">KLV Roofing</div>
  </section>
</main>
</body>
</html>
```